VENTURE CAPITAL GROUP BUSINESS CARD DESIGN

Venture Capital Group based in SF looking for a bold business card design. No trendy colour explosion, 3D effects etc. Just "simple" optical effects. Works on your brain, keeps your eye focused and sticks to your mind.
Target Market(s)
Technology startups
Industry/Entity Type
Venture Capital
Contact Information for Business Card
DESMOND WHITLAKE
MANAGING PARTNER
187 FENWORTH ST SAN FRANCISCO, CA 94187
415.555.0142 O
415.555.0147 F
415.555.0193 C
desmond@veldtmoorcapital.ventures

```html
<!DOCTYPE html>
<html lang="en">
<head>
<meta charset="utf-8">
<title>Veldtmoor Capital Group – Business Card</title>
<link rel="stylesheet" href="https://fonts.googleapis.com/css2?family=Source+Sans+3:ital,wght@0,400;0,600;1,400&display=swap">
<style>
  :root {
    --backdrop: #8c8c8c;
    --paper: #f1f1f1;
    --brand-green: #0f5a1e;
    --brand-green-deep: #063a12;
    --brand-green-light: #2f8a3a;
    --ink: #555555;
    --ink-soft: #7a7a7a;
    --mark-grey: #dcdcdc;
    --on-green: #ffffff;
  }
  * { margin: 0; padding: 0; box-sizing: border-box; }
  html, body {
    width: 1105px;
    height: 1200px;
    overflow: hidden;
    background: var(--backdrop);
    font-family: "Source Sans 3", "Myriad Pro", Arial, sans-serif;
  }
  .canvas {
    position: relative;
    width: 1105px;
    height: 1200px;
  }
  .card {
    position: absolute;
    left: 180px;
    width: 746px;
    height: 427px;
  }
  .card--front {
    top: 119px;
    background: var(--paper);
  }
  .card--back {
    top: 637px;
    background: radial-gradient(ellipse 60% 65% at 50% 50%, var(--brand-green-light) 0%, var(--brand-green) 55%, var(--brand-green-deep) 100%);
  }
  .holder-name {
    position: absolute;
    left: 38px;
    top: 30px;
    font-size: 27px;
    font-weight: 600;
    color: var(--brand-green);
  }
  .holder-title {
    position: absolute;
    left: 39px;
    top: 62px;
    font-size: 20px;
    color: var(--ink-soft);
  }
  .address {
    position: absolute;
    left: 39px;
    top: 212px;
    font-size: 19px;
    line-height: 28px;
    color: var(--ink);
  }
  .contact-list {
    position: absolute;
    left: 39px;
    top: 277px;
    list-style: none;
    font-size: 19px;
    line-height: 28.5px;
    color: var(--ink);
  }
  .contact-list li {
    display: flex;
    align-items: center;
    gap: 9px;
  }
  .contact-icon {
    width: 19px;
    height: 19px;
    fill: var(--brand-green-deep);
    flex: none;
  }
  .brand-front {
    position: absolute;
    left: 470px;
    top: 170px;
    width: 240px;
    text-align: center;
  }
  .brand-disc {
    display: block;
    width: 104px;
    height: 104px;
    margin: 0 auto 18px;
    border-radius: 50%;
    background: var(--mark-grey);
  }
  .brand-name {
    font-size: 21px;
    font-weight: 600;
    color: var(--brand-green);
    white-space: nowrap;
  }
  .brand-back {
    position: absolute;
    left: 0;
    right: 0;
    top: 95px;
    text-align: center;
  }
  .brand-back .brand-disc {
    width: 150px;
    height: 150px;
    margin-bottom: 20px;
  }
  .brand-back .brand-name {
    font-size: 30px;
    color: var(--on-green);
  }
  .website {
    position: absolute;
    left: 0;
    right: 0;
    top: 348px;
    text-align: center;
    font-size: 21px;
    font-style: italic;
    letter-spacing: 1.5px;
    color: var(--on-green);
  }
</style>
</head>
<body>
<main class="canvas">
  <section class="card card--front" aria-label="Business card front">
    <h1 class="holder-name">Desmond Whitlake</h1>
    <p class="holder-title">Managing Partner</p>
    <address class="address">187 Fenworth ST<br>San Francisco, CA 94187</address>
    <ul class="contact-list">
      <li>
        <svg class="contact-icon" viewBox="0 0 24 24" aria-hidden="true"><path d="M6.6 10.8a15.1 15.1 0 0 0 6.6 6.6l2.2-2.2c.3-.3.7-.4 1-.2 1.1.4 2.3.6 3.6.6.6 0 1 .4 1 1V20c0 .6-.4 1-1 1A17 17 0 0 1 3 4c0-.6.4-1 1-1h3.5c.6 0 1 .4 1 1 0 1.3.2 2.5.6 3.6.1.3 0 .7-.2 1z"/></svg>
        <span>415.555.0142</span>
      </li>
      <li>
        <svg class="contact-icon" viewBox="0 0 24 24" aria-hidden="true"><path d="M7 1h10c1.1 0 2 .9 2 2v18c0 1.1-.9 2-2 2H7c-1.1 0-2-.9-2-2V3c0-1.1.9-2 2-2zm0 3v14h10V4zm5 15.5a1.2 1.2 0 1 0 0 2.4 1.2 1.2 0 0 0 0-2.4z"/></svg>
        <span>415.555.0193</span>
      </li>
      <li>
        <svg class="contact-icon" viewBox="0 0 24 24" aria-hidden="true"><path d="M6 2h10l2 2v5H6zM4 10h16c1.1 0 2 .9 2 2v7H2v-7c0-1.1.9-2 2-2zm2 3v2h4v-2zm-4 7h20v2H2z"/></svg>
        <span>415.555.0147</span>
      </li>
      <li>
        <svg class="contact-icon" viewBox="0 0 24 24" aria-hidden="true"><path d="M2 5h20v14H2zm2 2v.5l8 5.5 8-5.5V7zm0 2.9V17h16V9.9l-8 5.5z"/></svg>
        <span>desmond@veldtmoorcapital.ventures</span>
      </li>
    </ul>
    <div class="brand-front">
      <span class="brand-disc" aria-hidden="true"></span>
      <p class="brand-name">Veldtmoor Capital Group</p>
    </div>
  </section>

  <section class="card card--back" aria-label="Business card back">
    <div class="brand-back">
      <span class="brand-disc" aria-hidden="true"></span>
      <p class="brand-name">Veldtmoor</p>
    </div>
    <p class="website">www.veldtmoorcapital.ventures</p>
  </section>
</main>
</body>
</html>
```